Website design needed for gift based dropship website

I am building a dropshipping website that will create gift based merchandise and send it out to our clients customers for them. Our clients will sell products and when a customer buys from them, we create the item and send it out to the customer.

I am looking for a very similar website to stitchora.com - that website is doing a very similar thing to what i am doing but where the stitchora website is based around clothing, my website will be based around gifts. Another website that i like that is doing a similar thing to what i will do is pelvane.com

I require 2 pages to be made:
1) The home page
2) A landing page for a free product giveaway offer

1) THE HOME PAGE
The home page should be a merger of the two previously stated websites (www.pelvane.com and www.stitchora.com). The style fo the homepage should be based on the logo that is attached and the colour scheme should be similar but basic.

2) THE LANDING PAGE
The landing page will be giving away a free mobile phone cover. The page needs to have some mobile phone covers for different phones all with random designs on. The page should state that they can have any design that they want and they do not pay for the phone (they only pay for shipping).

Menu pages and text should be taken from the stitchora.com website.

Target Market(s)

18 - 40 year old males. People who like the idea of earning extra money in their spare time but aren't too sure how to do it. Semi-professional jobs.

Font styles to use
Serif
Sans Serif
Decorative
Script

Colors

Designer to choose colors to be used in the design.

Requirements
Must have
• A "how it works" image where the dropshipping process is explained to a visitor to the website (similar to the one on the stitchora "how it works page")
Nice to have
• Testimonial area on homepage
Should not have
• Homepage should not have:
• - "latest orders from" area
• - Video
• - Warehousing/fulfilment area
• - Integration area

```html
<!DOCTYPE html>
<html lang="en">
<head>
<meta charset="utf-8">
<title>Keepsake Press – Personalised Gifts</title>
<link href="https://fonts.googleapis.com/css2?family=Roboto+Condensed:wght@400;700&family=Questrial&family=Open+Sans:ital,wght@0,400;0,600;0,700;1,400&display=swap" rel="stylesheet">
<style>
:root{
  --red:#e8352a;
  --maroon:#5a1a1f;
  --ink:#222;
  --white:#fff;
  --grey-bg:#f3f3f3;
  --field:#e4e4e4;
  --footer:#343434;
  --muted:#9a9a9a;
}
*{box-sizing:border-box;margin:0;padding:0}
html,body{width:1200px;height:2795px;overflow:hidden}
body{position:relative;background:var(--white);font-family:"Open Sans",sans-serif;color:var(--ink)}
.abs{position:absolute}
a{color:inherit;text-decoration:none}

/* header */
.site-header{position:absolute;left:0;top:0;width:1200px;height:104px;background:var(--white)}
.nav-link{position:absolute;top:44px;font-size:11px;letter-spacing:.3px;text-transform:uppercase;color:#333;font-family:"Open Sans",sans-serif}
.nav-link.active{color:var(--red)}
.nav-sep{position:absolute;top:41px;font-size:13px;color:#333}
.brand{position:absolute;left:528px;top:26px;display:flex;align-items:center;gap:8px;font-family:"Roboto Condensed",sans-serif;font-weight:700;font-size:24px;color:var(--maroon);text-transform:uppercase;line-height:1}
.brand-name{display:block}
.brand-dot{width:40px;height:40px;border-radius:50%;background:var(--maroon);flex:none}

/* hero */
.hero{position:absolute;left:0;top:104px;width:1200px;height:624px;background:radial-gradient(ellipse at 78% 45%,#8a4a32 0%,#4a2a1c 30%,#2a1a12 60%,#1a120c 100%)}
.hero-eyebrow{position:absolute;left:0;width:1200px;top:205px;text-align:center;color:var(--white);font-family:"Questrial",sans-serif;font-size:20px;letter-spacing:.5px}
.hero-title{position:absolute;left:333px;top:254px;width:533px;height:83px;border:2px solid var(--red);color:var(--white);font-family:"Roboto Condensed",sans-serif;font-weight:700;font-size:52px;text-align:center;line-height:79px;letter-spacing:.5px}
.btn{position:absolute;display:block;text-align:center;font-size:10px;text-transform:uppercase;font-weight:600;letter-spacing:.3px}
.btn-red{background:var(--red);color:var(--white)}
.btn-white{background:var(--white);color:#222}
.btn-black{background:#1d1d1d;color:var(--white)}

/* section headings */
.section-title{position:absolute;left:0;width:1200px;text-align:center;font-family:"Questrial",sans-serif;font-size:33px;font-weight:700}
.section-title .hl{color:var(--red)}

/* how it works */
.how{position:absolute;left:0;top:728px;width:1200px;height:465px;background:var(--white)}
.step-label{position:absolute;top:385px;width:200px;text-align:center;font-size:13px;font-weight:700;color:var(--maroon)}

/* difference */
.diff{position:absolute;left:0;top:1193px;width:1200px;height:576px;background:linear-gradient(100deg,#2c3230 0%,#4a4040 35%,#6a3634 55%,#3c3c3e 75%,#2e3034 100%)}
.diff-shade{position:absolute;inset:0;background:rgba(30,30,32,.45)}
.diff .section-title{color:var(--white);top:58px}
.brand-panel{position:absolute;left:222px;top:159px;width:347px;height:304px;background:#ececec;display:flex;align-items:center;justify-content:center;gap:14px}
.brand-panel .brand-dot{width:62px;height:62px}
.brand-panel-name{font-family:"Roboto Condensed",sans-serif;font-weight:700;font-size:44px;color:var(--maroon);text-transform:uppercase;line-height:1}
.feature{position:absolute;left:606px;width:520px;color:var(--white)}
.feature-title{font-size:20px;font-weight:600;text-transform:uppercase;letter-spacing:.2px}
.feature-title .slash{color:var(--red);font-weight:400;margin-right:8px}
.feature-text{font-size:11px;margin-top:2px;padding-left:20px}

/* products & testimonials */
.products{position:absolute;left:191px;top:1787px;width:366px;height:355px;background:var(--red);color:var(--white)}
.products-title{position:absolute;right:30px;top:72px;font-family:"Open Sans",sans-serif;font-weight:600;font-size:21px;text-transform:uppercase}
.product-link{position:absolute;right:30px;font-size:9.5px;font-weight:700;text-transform:uppercase;border-bottom:2px solid var(--white);padding-bottom:3px}
.testimonials-title{position:absolute;left:618px;top:1860px;font-size:20px;font-weight:600;text-transform:uppercase}
.testimonials-title .slash{color:var(--red);font-weight:400;margin-right:8px}
.quote-mark{position:absolute;left:618px;top:1900px;font-family:Georgia,serif;font-size:52px;color:#bbb;line-height:1}
.testimonial-text{position:absolute;left:618px;top:1946px;width:420px;font-style:italic;font-size:20.5px;line-height:27px;color:var(--muted)}

/* gallery */
.gallery-tile{position:absolute;top:2142px;height:236px}

/* signup */
.signup{position:absolute;left:0;top:2378px;width:1200px;height:231px;background:var(--grey-bg)}
.signup .section-title{top:55px;font-size:34px;color:#1c1c1c}
.tab{position:absolute;top:124px;height:30px;line-height:30px;text-align:center;font-size:11px;font-weight:600;background:var(--field);color:#222}
.tab.active{background:var(--red);color:var(--white)}
.field{position:absolute;top:187px;width:206px;height:28px;background:var(--field);font-size:10px;color:#999;padding-left:8px;line-height:28px}
.signup-btn{position:absolute;left:858px;top:187px;width:119px;height:28px;line-height:28px;text-align:center;background:var(--red);color:var(--white);font-size:12px;font-weight:600;text-transform:uppercase}

/* footer */
.site-footer{position:absolute;left:0;top:2609px;width:1200px;height:186px;background:var(--footer);color:#ddd}
.site-footer .brand{left:162px;top:64px;color:var(--white);font-size:24px}
.site-footer .brand-dot{background:var(--white);width:38px;height:38px}
.footer-link{position:absolute;top:96px;font-size:10px;text-transform:uppercase;letter-spacing:.3px}
.footer-sep{position:absolute;top:94px;font-size:11px;color:#888}
.social{position:absolute;top:86px;width:26px;height:26px;border:1px solid #888;background:#2a2a2a}
.footer-rule{position:absolute;left:0;top:149px;width:1200px;height:1px;background:#4a4a4a}
.copyright{position:absolute;left:0;width:1200px;top:163px;text-align:center;font-size:9px;color:#aaa}
</style>
</head>
<body>

<header class="site-header">
  <a class="nav-link active" style="left:161px">Pricing</a>
  <span class="nav-sep" style="left:234px">|</span>
  <a class="nav-link" style="left:266px">How it works</a>
  <span class="nav-sep" style="left:381px">|</span>
  <a class="nav-link" style="left:413px">Resource</a>
  <div class="brand"><span class="brand-dot"></span><span class="brand-name">Keepsake<br>Press</span></div>
  <a class="nav-link" style="left:734px">Mock up generator</a>
  <span class="nav-sep" style="left:885px">|</span>
  <a class="nav-link" style="left:917px">FAQ</a>
  <span class="nav-sep" style="left:970px">|</span>
  <a class="nav-link" style="left:1000px">Blogs</a>
</header>

<section class="hero" role="img" aria-label="Woman smiling as she opens a glowing red gift box with sparkles, warm blurred background">
  <div class="hero-eyebrow">KEEPSAKE PRESS</div>
  <h1 class="hero-title">PERSONALISED GIFTS</h1>
  <a class="btn btn-red" style="left:467px;top:386px;width:126px;height:30px;line-height:30px">Start</a>
  <a class="btn btn-white" style="left:607px;top:386px;width:162px;height:30px;line-height:30px">Connect your shop</a>
</section>

<section class="how">
  <h2 class="section-title" style="top:62px;color:#1c1c1c">How It <span class="hl">Works</span></h2>
  <svg class="abs" style="left:0;top:0" width="1200" height="465" viewBox="0 0 1200 465">
    <g fill="none" stroke="#3a1a1c" stroke-width="1.5">
      <polyline points="298,84 161,84 161,122"/>
      <polyline points="902,84 1038,84 1038,122"/>
    </g>
    <g fill="none" stroke="#4a1c20" stroke-width="2">
      <polygon points="256,155 344,206 344,308 256,359 168,308 168,206"/>
      <polygon points="491,155 579,206 579,308 491,359 403,308 403,206"/>
      <polygon points="716,155 804,206 804,308 716,359 628,308 628,206"/>
      <polygon points="944,155 1032,206 1032,308 944,359 856,308 856,206"/>
    </g>
    <g fill="none" stroke="#bbb" stroke-width="1">
      <polygon points="260,150 356,210 356,312 260,368 172,312"/>
      <polygon points="786,150 796,330 710,368"/>
    </g>
    <g fill="var(--red)">
      <polygon points="256,157 347,338 165,338"/>
      <polygon points="438,162 596,257 438,352"/>
      <polygon points="782,162 622,257 782,352"/>
      <polygon points="851,177 1036,177 944,338"/>
    </g>
    <g fill="var(--white)">
      <circle cx="256" cy="250" r="11"/>
      <path d="M238 286 q18 -22 36 0 z"/>
      <path d="M230 292 h38 q8 0 10 -6 l4 6 q-6 10 -16 10 h-36 z"/>
      <path d="M470 238 h44 l6 14 h-56 z"/>
      <rect x="470" y="254" width="44" height="28"/>
      <rect x="486" y="264" width="12" height="18" fill="var(--red)"/>
      <circle cx="716" cy="257" r="24"/>
      <path d="M922 240 h8 v14 l12 -8 v8 l12 -8 v8 l12 -8 v28 h-44 z"/>
      <rect x="928" y="262" width="6" height="6" fill="var(--red)"/>
      <rect x="940" y="262" width="6" height="6" fill="var(--red)"/>
      <rect x="952" y="262" width="6" height="6" fill="var(--red)"/>
    </g>
  </svg>
  <div class="step-label" style="left:156px">Marlo</div>
  <div class="step-label" style="left:370px">Your Store</div>
  <div class="step-label" style="left:616px">Keepsake Press</div>
  <div class="step-label" style="left:828px">Your Product Factory</div>
</section>

<section class="diff" role="img" aria-label="Person in a red sweater holding striped wrapped gift boxes beside a Christmas tree, darkened">
  <div class="diff-shade"></div>
  <h2 class="section-title">What Makes Us <span class="hl">Different</span></h2>
  <svg class="abs" style="left:0;top:0" width="1200" height="140" viewBox="0 0 1200 140">
    <g fill="none" stroke="#ddd" stroke-width="1.5">
      <polyline points="298,82 161,82 161,120"/>
      <polyline points="902,82 1038,82 1038,120"/>
    </g>
  </svg>
  <div class="brand-panel"><span class="brand-dot"></span><span class="brand-panel-name">Keepsake<br>Press</span></div>
  <div class="feature" style="top:168px"><div class="feature-title"><span class="slash">/</span>Three Fulfillment Locations</div><p class="feature-text">We're located on both sides of the big pond to bring you closer to your customers</p></div>
  <div class="feature" style="top:241px"><div class="feature-title"><span class="slash">/</span>Free Signup, No Monthly Fees</div><p class="feature-text">You only pay when you submit an order, and only for the products you order</p></div>
  <div class="feature" style="top:314px"><div class="feature-title"><span class="slash">/</span>No Minimums</div><p class="feature-text">You only pay when you submit an order, and only for the products you order</p></div>
  <div class="feature" style="top:387px"><div class="feature-title"><span class="slash">/</span>Automated Order Import</div><p class="feature-text">You only pay when you submit an order, and only for the products you order</p></div>
</section>

<section class="products">
  <h3 class="products-title">Our Products&nbsp; /</h3>
  <a class="product-link" style="top:128px">Lorem ipsum</a>
  <a class="product-link" style="top:164px">Lorem ipsum dolor sit</a>
  <a class="product-link" style="top:200px">Dolor sit amet</a>
  <a class="product-link" style="top:236px">Lorem ipdum dolor sit..</a>
  <a class="btn btn-white" style="left:27px;top:281px;width:182px;height:24px;line-height:24px;font-size:9.5px">Print designs for yourself</a>
  <a class="btn btn-black" style="left:209px;top:281px;width:138px;height:24px;line-height:24px;font-size:9.5px">Sell designs online</a>
</section>
<h3 class="testimonials-title"><span class="slash">/</span>Testimonials</h3>
<div class="quote-mark">&ldquo;</div>
<p class="testimonial-text">Lorem ipsum dolor sit amet, consectetu adipiscing elit, sed do eiusmod tempor incididunt ut labore et dolore magna aliqua. Ut enim ad minim veniam, quis nostrud</p>
<a class="btn btn-black" style="left:618px;top:2068px;width:91px;height:24px;line-height:24px;font-size:9.5px">View more</a>

<div class="gallery-tile" style="left:0;width:311px;background:linear-gradient(160deg,#9ab0c0 0%,#c8b8a8 45%,#b8403c 100%)" role="img" aria-label="Woman in a knitted hat holding a stack of gift boxes"></div>
<div class="gallery-tile" style="left:311px;width:288px;background:linear-gradient(160deg,#f2ece4 0%,#d8c4b0 55%,#c84a40 100%)" role="img" aria-label="Open hands holding a small white gift box with a red bow"></div>
<div class="gallery-tile" style="left:599px;width:283px;background:linear-gradient(150deg,#6cc8c4 0%,#7fd0cc 45%,#d4a048 70%,#c8403a 100%)" role="img" aria-label="Hands holding a gold gift box with a red ribbon on a teal background"></div>
<div class="gallery-tile" style="left:882px;width:318px;background:linear-gradient(160deg,#d83a30 0%,#e44a3c 50%,#c8a07a 100%)" role="img" aria-label="Person in red holding stacked striped and kraft paper gifts"></div>

<section class="signup">
  <h2 class="section-title">Create your Account for <span class="hl">FREE</span></h2>
  <div class="tab active" style="left:278px;width:192px">No sign-up &amp; no monthly fees</div>
  <div class="tab" style="left:498px;width:196px">Discounts on sample orders</div>
  <div class="tab" style="left:726px;width:193px">More time for yourself</div>
  <div class="field" style="left:218px">Full Name</div>
  <div class="field" style="left:432px">Email</div>
  <div class="field" style="left:645px">Password</div>
  <div class="signup-btn">Sing up</div>
</section>

<footer class="site-footer">
  <div class="brand"><span class="brand-dot"></span><span class="brand-name">Keepsake<br>Press</span></div>
  <a class="footer-link" style="left:411px">Products</a>
  <span class="footer-sep" style="left:476px">|</span>
  <a class="footer-link" style="left:494px">How it works</a>
  <span class="footer-sep" style="left:581px">|</span>
  <a class="footer-link" style="left:598px">Resources</a>
  <span class="footer-sep" style="left:667px">|</span>
  <a class="footer-link" style="left:688px">FAQ</a>
  <span class="footer-sep" style="left:718px">|</span>
  <a class="footer-link" style="left:736px">Blog</a>
  <span class="footer-sep" style="left:772px">|</span>
  <a class="footer-link" style="left:790px">Contact us</a>
  <span class="social" style="left:888px"></span>
  <span class="social" style="left:918px"></span>
  <span class="social" style="left:948px"></span>
  <span class="social" style="left:978px"></span>
  <span class="social" style="left:1008px"></span>
  <div class="footer-rule"></div>
  <p class="copyright">Copyright © 2018 Keepsake Press. All Rights Reserved.</p>
</footer>

</body>
</html>
```